Veldmark Supplies Business Card

Professional business card that stand out to our potential customers. Front and back with clean modern design

Industry/Entity Type

Oil and gas

Contact Information for Business Card

Name, address, website , office phone and cell number

Requirements
Must have
• Editable files for each employee

```html
<!DOCTYPE html>
<html lang="en">
<head>
<meta charset="utf-8">
<title>Veldmark Supplies Business Card</title>
<link href="https://fonts.googleapis.com/css2?family=Montserrat:wght@400;500;700;800&display=swap" rel="stylesheet">
<style>
  :root {
    --card-blue: #06aed5;
    --card-blue-deep: #0593b5;
    --brand-red: #ee0a14;
    --paper: #ffffff;
    --stage: #ecebe8;
  }
  * { box-sizing: border-box; margin: 0; padding: 0; }
  html, body { width: 1200px; height: 878px; overflow: hidden; }
  body {
    background: var(--stage);
    font-family: "Montserrat", sans-serif;
    position: relative;
  }
  .card {
    position: absolute;
    top: 107px;
    width: 380px;
    height: 664px;
    border-radius: 34px;
    overflow: hidden;
    box-shadow: 0 10px 24px rgba(0,0,0,.18);
  }
  /* Back side */
  .card-back { left: 180px; background: var(--card-blue); }
  .back-brand {
    position: absolute;
    left: 50%; top: 50%;
    transform: translate(-50%, -50%) rotate(90deg);
    display: flex; align-items: center; gap: 18px;
    white-space: nowrap;
  }
  .back-brand .mark-square {
    width: 30px; height: 30px; background: var(--paper);
  }
  .back-brand .brand-name {
    color: var(--paper);
    font-weight: 800;
    font-size: 36px;
    letter-spacing: 3px;
  }
  /* Front side */
  .card-front { left: 640px; background: var(--card-blue); }
  .front-top {
    position: absolute; inset: 0;
    background: var(--paper);
    clip-path: polygon(0 0, 100% 0, 100% 22%, 0 44%);
  }
  .front-brand {
    position: absolute; top: 34px; left: 0; right: 0;
    display: flex; justify-content: center; align-items: center; gap: 12px;
  }
  .front-brand .mark-square { width: 22px; height: 22px; background: var(--brand-red); }
  .front-brand .brand-name {
    color: var(--brand-red);
    font-weight: 800; font-size: 26px; letter-spacing: 2px;
  }
  .person {
    position: absolute; top: 330px; left: 0; right: 0;
    text-align: center; color: var(--paper);
  }
  .person-name { font-weight: 800; font-size: 27px; letter-spacing: 1px; }
  .person-role {
    display: flex; align-items: center; justify-content: center; gap: 12px;
    font-size: 17px; font-weight: 500; margin-top: 2px;
  }
  .person-role::before, .person-role::after {
    content: ""; width: 70px; height: 2px; background: var(--paper);
  }
  .contact-icons {
    position: absolute; top: 420px; left: 0; right: 0;
    display: flex; justify-content: center; gap: 18px;
  }
  .icon-box {
    width: 34px; height: 34px; background: var(--brand-red);
    display: flex; align-items: center; justify-content: center;
  }
  .icon-box svg { width: 20px; height: 20px; }
  .contact-lines {
    position: absolute; top: 474px; left: 0; right: 0;
    text-align: center; color: var(--paper);
    font-size: 16px; line-height: 1.45;
  }
  .divider {
    width: 260px; height: 1.5px; background: var(--paper);
    margin: 12px auto;
  }
</style>
</head>
<body>
  <section class="card card-back" aria-label="Card back">
    <div class="back-brand">
      <span class="mark-square"></span>
      <span class="brand-name">VELDMARK SUPPLIES</span>
    </div>
  </section>

  <section class="card card-front" aria-label="Card front">
    <div class="front-top"></div>
    <div class="front-brand">
      <span class="mark-square"></span>
      <span class="brand-name">VELDMARK SUPPLIES</span>
    </div>

    <div class="person">
      <p class="person-name">DORRAN KELLBY</p>
      <p class="person-role">President</p>
    </div>

    <div class="contact-icons">
      <span class="icon-box" aria-label="Office phone">
        <svg viewBox="0 0 24 24" fill="#fff"><path d="M3 9c0-3 4-5 9-5s9 2 9 5l-1 2-4-1V8c-2-1-6-1-8 0v2l-4 1zM6 13h12l2 7H4z"/></svg>
      </span>
      <span class="icon-box" aria-label="Mobile phone">
        <svg viewBox="0 0 24 24" fill="none" stroke="#fff" stroke-width="2"><rect x="7" y="2" width="10" height="20" rx="2"/><circle cx="12" cy="18" r="1" fill="#fff"/></svg>
      </span>
      <span class="icon-box" aria-label="Email">
        <svg viewBox="0 0 24 24" fill="none" stroke="#fff" stroke-width="2"><rect x="2" y="5" width="20" height="14"/><path d="M2 5l10 8 10-8"/></svg>
      </span>
      <span class="icon-box" aria-label="Website">
        <svg viewBox="0 0 24 24" fill="none" stroke="#fff" stroke-width="2"><circle cx="12" cy="12" r="9"/><path d="M3 12h18M12 3c3 3 3 15 0 18M12 3c-3 3-3 15 0 18"/></svg>
      </span>
    </div>

    <div class="contact-lines">
      <p>555-014-2290</p>
      <p>000-000-9999</p>
      <p>info@example-youremail.com</p>
      <p>www.example-yourwebsite.com</p>
      <div class="divider"></div>
      <p>420 Harlow Ridge Rd, Ste 210,</p>
      <p>Calloway, TX 79990</p>
    </div>
  </section>
</body>
</html>
```